Stationery Design + Business Cards

Stationary (letterhead as A4 210x297mm and Letter 8.5"x11", preferably both master page + 2nd pages)

Also need business cards, standard size 50x88mm, can be vertical or horizontal.

You can use a front/back design for the business cards, or front only.

Looking at the uploaded file (devank, you already have that), I want it to use the first logo on the list (4 colors).

Alternative, try the grayscale version (second file).

I need the following information on the business card (in no particular order, let me know what you come up with): 

Firstname Lastlame 
Title 

Mobile +1 555-204-7391 

VelaMorn, Inc. 
24851 Birchwood Ridge Passage 
Carmel, IN 46099 
Tel. +1 555-368-4172 
Fax +1 555-619-0834 

Web: www.velamorn.example 
Twitter: twitter/VelaMorn or @VelaMorn 
Facebook: facebook.com/VelaMorn 

For letterhead, just the company name, address + phone number & fax number 

If you think the phone/fax or something else should not be on the business cards, or something could be missing, let me know.

```html
<!DOCTYPE html>
<html lang="en">
<head>
<meta charset="utf-8">
<title>VelaMorn Letterhead 8.5x11</title>
<link rel="stylesheet" href="https://fonts.googleapis.com/css2?family=Source+Sans+3:wght@400;700&display=swap">
<style>
  :root {
    --stage: #000000;
    --paper: #ffffff;
    --brand-blue: #1a4f9e;
    --footer-blue: #124d9f;
    --rule-grey: #c9cbcd;
    --accent-orange: #f07a21;
    --decor-grey: #edeeee;
    --label-white: #ffffff;
  }
  * { margin: 0; padding: 0; box-sizing: border-box; }
  html, body {
    width: 900px;
    height: 1200px;
    overflow: hidden;
    background: var(--stage);
    font-family: "Source Sans 3", "Myriad Pro", Arial, sans-serif;
  }
  .presentation {
    position: relative;
    width: 900px;
    height: 1200px;
  }
  .format-label {
    position: absolute;
    top: 85px;
    left: 0;
    width: 900px;
    text-align: center;
    color: var(--label-white);
    font-weight: 700;
    font-size: 19px;
    line-height: 24px;
  }
  .letterhead {
    position: absolute;
    left: 40px;
    top: 119px;
    width: 822px;
    height: 1064px;
    background: var(--paper);
    overflow: hidden;
  }
  .corner-decor {
    position: absolute;
    left: 0;
    top: 0;
    width: 500px;
    height: 460px;
    background: radial-gradient(ellipse 100% 100% at 0% 0%, var(--decor-grey) 0%, var(--decor-grey) 55%, rgba(237,238,238,0) 100%);
  }
  .brand {
    position: absolute;
    left: 516px;
    top: 72px;
    display: flex;
    align-items: center;
    gap: 10px;
  }
  .brand-dot {
    width: 40px;
    height: 40px;
    border-radius: 50%;
    background: var(--accent-orange);
  }
  .brand-name {
    color: var(--brand-blue);
    font-weight: 400;
    font-size: 52px;
    line-height: 1;
    letter-spacing: -0.3px;
  }
  .footer-rule {
    position: absolute;
    left: 0;
    bottom: 34px;
    width: 100%;
    height: 4px;
    background: var(--rule-grey);
  }
  .footer-band {
    position: absolute;
    left: 0;
    bottom: 0;
    width: 100%;
    height: 32px;
    background: var(--footer-blue);
    display: flex;
    align-items: center;
    justify-content: center;
  }
  .footer-address {
    color: var(--paper);
    font-weight: 700;
    font-size: 11px;
  }
</style>
</head>
<body>
  <main class="presentation">
    <h1 class="format-label">Letter Head 8.5x11 Inch</h1>
    <section class="letterhead">
      <div class="corner-decor" role="img" aria-label="Soft grey brand decoration area"></div>
      <div class="brand">
        <span class="brand-dot"></span>
        <span class="brand-name">VelaMorn</span>
      </div>
      <div class="footer-rule"></div>
      <footer class="footer-band">
        <p class="footer-address">VelaMorn, Inc., 24851 Birchwood Ridge Passage, Carmel, IN 46099, Tel. +1 555-368-4172, Fax +1 555-619-0834</p>
      </footer>
    </section>
  </main>
</body>
</html>
```